Northvale Strategy Partners Website Design

I need a website design for my new business consulting and executive coaching firm, Northvale Strategy Partners. We provide consultative services to business C-suites as well as personal coaching to executives. I have attached the logo with color scheme I have chosen. I would like the website to reflect professionalism and continue the color scheme in the logo.

Target Market(s)

Small to medium business and their executives; middle to upper income men and women in mid- to late career looking for significance

Industry/Entity Type

Business Consultant

Number of Pages Required

4 page

Requirements
Must have
• A homepage with prominent logo and way to contact for more information; an area on the homepage with easy to read, clear text to describe what the company does; a prominent area on the homepage for a tagline; a blog page that can be updated regularly, an "about us" page with biographical information; an "about us" page; a page detailing services offered
• The web design must match the logo colors and font that I have uploaded.
Nice to have
• A lighthouse picture in the background or header
Should not have
• A lot of text area on the homepage

```html
<!DOCTYPE html>
<html lang="en">
<head>
<meta charset="utf-8">
<title>Northvale Strategy Partners</title>
<link rel="stylesheet" href="https://fonts.googleapis.com/css2?family=Roboto+Slab:wght@300;400&family=Roboto:wght@400;500&display=swap">
<style>
:root{
  --navy:#1f2b4d;
  --white:#ffffff;
  --soft:#e8ecf3;
  --sky-top:#27405f;
  --sky-mid:#7b95b8;
  --sky-low:#d9dfe7;
  --slate:#3f4145;
  --slate-2:#56585c;
  --steel-1:#2f4672;
  --steel-2:#5a6f98;
  --rose-1:#9a4b4f;
  --rose-2:#b97676;
  --wine:#7a1d22;
  --footer:#2f2f2f;
  --muted:#a9a9a9;
  --line:rgba(255,255,255,.55);
}
*{box-sizing:border-box;margin:0;padding:0}
html,body{width:1200px;height:2875px;overflow:hidden}
body{font-family:"Roboto",Arial,sans-serif;color:var(--white);background:var(--footer);position:relative}
.section{position:absolute;left:0;width:1200px;overflow:hidden}
.abs{position:absolute}

/* hero */
.hero{top:0;height:656px;background:linear-gradient(180deg,var(--sky-top) 0%,var(--sky-mid) 45%,var(--sky-low) 75%,#f2f3f5 100%)}
.main-nav{top:18px;left:0;width:1200px;display:flex;justify-content:center;gap:34px;font-family:"Roboto Slab",serif;font-size:14px;letter-spacing:.5px}
.main-nav a{color:var(--white);text-decoration:none;padding-bottom:8px}
.main-nav a.active{border-bottom:1px solid var(--white)}
.main-nav .sep{font-size:8px;line-height:22px}
.lighthouse{left:800px;top:60px;width:130px;height:480px;background:linear-gradient(180deg,#cfd6c4,#8d9160 50%,#e9ece6);border-radius:30px 30px 0 0;opacity:.85}
.brand{left:360px;top:390px;width:480px;text-align:center;color:var(--navy);font-family:"Roboto Slab",serif;font-weight:400}
.brand .name{font-size:62px;letter-spacing:3px;line-height:1}
.brand .sub{font-size:28px;letter-spacing:4px;margin-top:8px}

/* who we are */
.who{top:656px;height:657px;background:linear-gradient(135deg,#3b3d41,var(--slate-2) 50%,#44464a)}
.who h2{left:80px;top:60px;font-family:"Roboto Slab",serif;font-weight:400;font-size:40px}
.who .intro{left:80px;top:120px;width:500px;font-size:15px;line-height:21px}
.feature{width:270px}
.feature .icon{width:46px;height:46px;border-radius:6px;margin-bottom:14px}
.feature h3{font-family:"Roboto Slab",serif;font-weight:400;font-size:17px;border-top:1px solid var(--line);padding-top:10px;width:100%}
.feature p{font-size:12.5px;line-height:20px;margin-top:10px;width:270px}
.puzzle{left:760px;top:215px;width:310px;height:250px;border-radius:24px;background:linear-gradient(135deg,#2f7fd8,#f2c400 40%,#e8341c 70%,#3db34a)}
.vert{writing-mode:vertical-rl;text-orientation:upright;white-space:nowrap;font-family:"Roboto Slab",serif;font-size:16px;line-height:20px;letter-spacing:3px}
.tag{font-family:"Roboto Slab",serif;font-size:17px;white-space:nowrap}

/* advice */
.advice{top:1313px;height:656px;background:linear-gradient(120deg,var(--steel-1),var(--steel-2) 55%,#3b5180)}
.advice .pitch{left:0;top:106px;width:1200px;text-align:center;font-family:"Roboto Slab",serif;font-weight:300;font-size:31px;line-height:52px}
.advice .pitch strong{font-weight:400;font-size:50px}
.advice h2{left:0;top:316px;width:1150px;text-align:center;font-family:"Roboto Slab",serif;font-weight:400;font-size:40px}
.newsletter{left:381px;top:405px;width:437px;height:50px;border:1px solid var(--line);background:rgba(255,255,255,.12);display:flex;align-items:center;justify-content:space-between;padding:0 16px;font-size:15px}
.subscribe{left:660px;top:540px;font-size:13px;transform:rotate(25deg);transform-origin:left}
.advisor{left:872px;top:287px;width:298px;height:369px;border-radius:140px 140px 0 0;background:linear-gradient(180deg,#b08a6a,#4d5360 55%,#3a3f4c)}

/* enquiry */
.enquiry{top:1969px;height:657px;background:linear-gradient(135deg,var(--rose-1),var(--rose-2) 60%,#a86262)}
.enquiry h2{left:0;top:58px;width:1200px;text-align:center;font-family:"Roboto Slab",serif;font-weight:400;font-size:42px}
.field{left:88px;width:499px;height:42px;border:1px solid rgba(255,255,255,.85);background:rgba(255,255,255,.08);display:flex;align-items:center;gap:12px;padding:0 16px;font-size:15px}
.message{left:611px;top:167px;width:501px;height:135px;border:1px solid rgba(255,255,255,.85);padding:14px 18px;font-size:15px}
.send{left:611px;top:314px;width:501px;height:50px;background:var(--white);color:var(--wine);display:flex;align-items:center;justify-content:space-between;padding:0 30px;font-size:19px}
.contact-item{width:300px;text-align:center;font-size:14px;line-height:22px}
.contact-item svg{display:block;margin:0 auto 14px}
.divider{left:77px;top:561px;width:1046px;height:1px;background:rgba(255,255,255,.5)}
.social{top:584px;left:512px;display:flex;gap:11px}
.social span{width:52px;height:52px;border-radius:50%;border:2px solid rgba(255,255,255,.8)}
.social span.on{background:var(--wine);border-color:var(--wine)}

/* footer */
.site-footer{top:2626px;height:249px;background:var(--footer)}
.site-footer h4{font-family:"Roboto Slab",serif;font-weight:400;font-size:19px}
.post{left:78px;width:350px;display:flex;gap:14px;font-size:13px;line-height:19px;color:var(--muted)}
.post .avatar{width:50px;height:50px;border-radius:50%;background:linear-gradient(135deg,#c9a27e,#6b5440);flex:none}
.post .time{margin-left:auto;color:var(--white)}
.post small{display:block;color:var(--white);font-size:12px}
.links{left:519px;top:76px;display:grid;grid-template-columns:114px 100px;row-gap:12px;font-size:14px;color:var(--muted)}
.links .active{color:var(--white)}
.foot-brand{left:880px;top:65px;width:160px;text-align:center;font-family:"Roboto Slab",serif;font-size:22px;letter-spacing:2px}
.copyright{left:832px;top:162px;font-size:12px}
.to-top{left:1133px;top:177px;width:50px;height:50px;border-radius:50%;border:2px solid var(--white);display:flex;align-items:center;justify-content:center}
</style>
</head>
<body>

<header class="section hero">
  <div class="abs lighthouse" role="img" aria-label="Lighthouse rising above clouds, beam of light"></div>
  <nav class="abs main-nav">
    <a class="active" href="#">HOME</a><span class="sep">◆</span>
    <a href="#">ABOUT</a><span class="sep">◆</span>
    <a href="#">SERVICES</a><span class="sep">◆</span>
    <a href="#">CONTACT</a>
  </nav>
  <div class="abs brand">
    <div class="name">NORTHVALE</div>
    <div class="sub">STRATEGY PARTNERS</div>
  </div>
</header>

<section class="section who" role="img" aria-label="Business team around a table with puzzle pieces, seen from above">
  <h2 class="abs">Who We Are</h2>
  <p class="abs intro">Lorem Ipsum is simply dummy text of the printing and typesetting industry. Lorem Ipsum has been the industry's standard dummy text ever since the 1500s, when an unknown printer took a galley of type and scrambled it to make a type specimen book.</p>

  <div class="abs feature" style="left:80px;top:258px">
    <div class="icon" role="img" aria-label="Target icon" style="background:#c9262c"></div>
    <h3>STRATEGY &amp; PLANNING</h3>
    <p>Lorem Ipsum is simply dummy text of the printing and typesetting industry</p>
  </div>
  <div class="abs feature" style="left:374px;top:258px">
    <div class="icon" role="img" aria-label="Folder icon" style="background:#e6b422"></div>
    <h3>PROJECT MANAGEMENT</h3>
    <p>Lorem Ipsum is simply dummy text of the printing and typesetting industry</p>
  </div>
  <div class="abs feature" style="left:80px;top:446px">
    <div class="icon" role="img" aria-label="Darts on target icon" style="background:#3a7fd0"></div>
    <h3>OBJECTIVE REVIEWS</h3>
    <p>Lorem Ipsum is simply dummy text of the printing and typesetting industry</p>
  </div>
  <div class="abs feature" style="left:374px;top:446px">
    <div class="icon" role="img" aria-label="Calculator and chart icon" style="background:#6e8fb5"></div>
    <h3>BUSINESS ANALYSIS</h3>
    <p>Lorem Ipsum is simply dummy text of the printing and typesetting industry</p>
  </div>

  <div class="abs vert" style="left:722px;top:168px">OBJECTIVE REVIEWS</div>
  <div class="abs tag" style="left:806px;top:162px">STRATEGY &amp; PLANNING</div>
  <div class="abs puzzle" role="img" aria-label="Four coloured puzzle pieces joined together"></div>
  <div class="abs tag" style="left:801px;top:472px">PROJECT MANAGEMENT</div>
  <div class="abs vert" style="left:1088px;top:168px">BUSINESS ANALYSIS</div>
</section>

<section class="section advice" role="img" aria-label="Modern glass and steel architecture in blue tones">
  <p class="abs pitch">Providing tailored <strong>Specialist ADVICE</strong> to<br>businesses, working together to identity problem areas,<br>resolve issues and improve performance.</p>
  <h2 class="abs">GET NEWSLETTER</h2>
  <div class="abs newsletter">
    <span>E-Mail</span>
    <svg width="30" height="20" viewBox="0 0 30 20" fill="none" stroke="#fff" stroke-width="1.5"><rect x="1" y="1" width="28" height="18"/><path d="M1 1l14 10L29 1M1 19l10-9M29 19l-10-9"/></svg>
  </div>
  <div class="abs subscribe">Subscribe Here</div>
  <div class="abs advisor" role="img" aria-label="Smiling businesswoman giving two thumbs up"></div>
</section>

<section class="section enquiry" role="img" aria-label="Hands signing a document with a pen">
  <h2 class="abs">Enquiry Form</h2>
  <div class="abs field" style="top:167px"><svg width="14" height="14" viewBox="0 0 14 14" fill="#fff"><circle cx="7" cy="4" r="3.5"/><path d="M0 14c0-4 3-6 7-6s7 2 7 6z"/></svg>Your Name</div>
  <div class="abs field" style="top:219px"><svg width="16" height="12" viewBox="0 0 16 12" fill="#fff"><path d="M0 0h16v12H0z"/><path d="M0 0l8 6 8-6" stroke="#a86262" fill="none"/></svg>Your E-mail Address</div>
  <div class="abs field" style="top:271px"><svg width="14" height="14" viewBox="0 0 14 14" fill="#fff"><path d="M3 0l3 3-2 2c1 2 3 4 5 5l2-2 3 3-2 3C6 14 0 8 0 3z"/></svg>Your Phone No.</div>
  <div class="abs field" style="top:323px"><svg width="16" height="12" viewBox="0 0 16 12" fill="#fff"><path d="M0 1c3-1 6 0 7.5 1v10C6 11 3 10 0 11zM16 1c-3-1-6 0-7.5 1v10c1.5-1 4.5-2 7.5-1z"/></svg>Subject</div>
  <div class="abs message">Your Message Here...</div>
  <div class="abs send"><span>Send Message</span><svg width="28" height="24" viewBox="0 0 28 24" fill="#7a1d22"><path d="M0 11L28 0 22 24 13 15 24 4 10 13z"/></svg></div>

  <div class="abs contact-item" style="left:124px;top:432px">
    <svg width="26" height="34" viewBox="0 0 26 34" fill="none" stroke="#fff" stroke-width="1.8"><path d="M13 33S1 19 1 12a12 12 0 0124 0c0 7-12 21-12 21z"/><circle cx="13" cy="12" r="4.5"/></svg>
    123 Street Name, Area, City, Country<br>Zipcode
  </div>
  <div class="abs contact-item" style="left:479px;top:432px">
    <svg width="30" height="30" viewBox="0 0 30 30" fill="none" stroke="#fff" stroke-width="1.8"><path d="M7 2l5 6-3 3c2 4 6 8 10 10l3-3 6 5-4 5C13 28 2 17 2 6z"/></svg>
    +00 123 4567 890
  </div>
  <div class="abs contact-item" style="left:835px;top:432px">
    <svg width="32" height="24" viewBox="0 0 32 24" fill="none" stroke="#fff" stroke-width="1.8"><rect x="1" y="1" width="30" height="22" rx="2"/><path d="M1 2l15 11L31 2"/></svg>
    info@northvale.com
  </div>

  <div class="abs divider"></div>
  <div class="abs social" aria-label="Social links">
    <span class="on"></span><span></span><span></span><span></span>
  </div>
</section>

<footer class="section site-footer">
  <h4 class="abs" style="left:80px;top:24px">Blog</h4>
  <div class="abs post" style="top:66px">
    <div class="avatar" role="img" aria-label="Author photo"></div>
    <div>Clara Denholm posted a new<br>blog.<small>Today 5:60 pm - 12.06.2014</small></div>
    <span class="time">5m ago</span>
  </div>
  <div class="abs post" style="top:140px">
    <div class="avatar" role="img" aria-label="Author photo"></div>
    <div>Peter Alcott posted<br>message on Clara Denholm<small>Today 2:10 pm - 12.06.2014</small></div>
    <span class="time">2h ago</span>
  </div>

  <h4 class="abs" style="left:523px;top:24px">Navigation Links</h4>
  <div class="abs links">
    <span class="active">Home</span><span>Class</span>
    <span>About</span><span>Blog</span>
    <span>Service</span><span>Terms</span>
    <span>Enquiry</span><span>Faq's</span>
    <span>Contact</span><span></span>
  </div>

  <div class="abs foot-brand">NORTHVALE</div>
  <div class="abs copyright">© 2015 NORTHVALE. All Rights Reserved.</div>
  <div class="abs to-top"><svg width="18" height="16" viewBox="0 0 18 16" fill="none" stroke="#fff" stroke-width="2.5"><path d="M9 2L2 14h14z"/></svg></div>
</footer>

</body>
</html>
```